Inspirational Quotes Poster Set

Brookloft is a stylish coworking space, which has a design-oriented vintage look from the 60's with an industrial touch (www.brookloft-example.com) Brookloft Quote Poster Set of 16 posters. The poster should be typo oriented and rather simple. Reflecting a bit the clean billboard design from the sixties. Minimal / simple graphical elements

Target Market(s)

Startups and Entrepreneurs

Industry/Entity Type

Startup

Font styles to use
Sans Serif

Colors

Designer to choose colors to be used in the design.

Requirements
Must have
• Posters need to be on and very stylish

```html
<!DOCTYPE html>
<html lang="en">
<head>
<meta charset="utf-8">
<title>Brookloft Quote Poster Set – Start Doing</title>
<link rel="stylesheet" href="https://fonts.googleapis.com/css2?family=Bebas+Neue&family=Open+Sans:wght@400&display=swap">
<style>
  :root {
    --poster-orange: #ff5000;
    --panel-grey: #bdbeb5;
    --ink: #000000;
  }
  html, body {
    margin: 0;
    padding: 0;
    width: 738px;
    height: 1200px;
    overflow: hidden;
    background: var(--poster-orange);
  }
  .poster {
    position: relative;
    width: 738px;
    height: 1200px;
    background: var(--poster-orange);
    overflow: hidden;
  }
  .quote-panel {
    position: absolute;
    left: 87px;
    top: 253px;
    width: 573px;
    height: 897px;
    background: var(--panel-grey);
  }
  .runner-icon {
    position: absolute;
    left: 45px;
    top: 18px;
    width: 374px;
    height: 280px;
    display: block;
  }
  .quote-line,
  .attribution-line {
    position: absolute;
    left: 87px;
    width: 573px;
    margin: 0;
    text-align: center;
    line-height: 1;
    color: var(--ink);
    white-space: nowrap;
  }
  .quote-line {
    font-family: "Bebas Neue", "Arial Narrow", sans-serif;
    font-weight: 400;
    letter-spacing: 0.02em;
  }
  .quote-line--lead    { top: 319px; font-size: 82px;  letter-spacing: 0.035em; }
  .quote-line--hero    { top: 403px; font-size: 152px; }
  .quote-line--link    { top: 562px; font-size: 74px; }
  .quote-line--strong  { top: 649px; font-size: 98px; }
  .quote-line--joiner  { top: 768px; font-size: 63px; }
  .quote-line--close   { top: 834px; font-size: 104px; }
  .attribution-line {
    font-family: "Open Sans", "Calibri", sans-serif;
    font-size: 30px;
    font-weight: 400;
  }
  .attribution-line--name  { top: 1008px; }
  .attribution-line--title { top: 1060px; }
</style>
</head>
<body>
  <main class="poster">
    <div class="quote-panel"></div>

    <svg class="runner-icon" viewBox="0 0 374 280" role="img" aria-label="Pictogram of a running figure with speed lines">
      <rect x="0" y="0" width="374" height="280" fill="#bdbeb5"/>
    </svg>

    <blockquote class="quote">
      <p class="quote-line quote-line--lead">The way to get</p>
      <p class="quote-line quote-line--hero">Started</p>
      <p class="quote-line quote-line--link">is to</p>
      <p class="quote-line quote-line--strong">Quit talking</p>
      <p class="quote-line quote-line--joiner">and</p>
      <p class="quote-line quote-line--close">Start doing.</p>
    </blockquote>

    <p class="attribution-line attribution-line--name">Wren Dalloway</p>
    <p class="attribution-line attribution-line--title">Co-Founder, Dalloway</p>
  </main>
</body>
</html>
```